Website development company website

ABOUT COMPANY
Hi everyone! We're a Melbourne, Australia website development company in a need of a website design that will make online store merchants want to engage our services.
We specialise exclusively in Torvista e-commerce platform (https://torvista-platform.example/). What distinguishes our business from competition is that rather than designing and building brand new websites, we offer development, support and maintenance services to established websites. Maintenance and Support are the keywords representing our business.
Our potential clients are people with broken, slow and underperforming Torvista installations who need assistance getting their websites up and making sales. Our website must pass the message that we can help, and provide quick means of making contact.
DESIGN
Overall, we're looking for a slick, clean, airy, conservative design. No need to do anything crazy, try to stick to what's "standard" in website design these days and make it easy on all of us. The website is unlikely to be updated too often so it needs to look attractive and fresh first time over and after a year, too.
Attached is our new logo, which you'll be able to take the basic idea from, the colors and fonts. Though, don't use the fonts from the logo in the website, stick to the standard widely supported fonts. Additional use of Google fonts is fine.
Don't overdo it with colors, stick to conservative basic color set and only use the colors from the log for accents like headings etc. Please, don't be tempted to use the blue and orange as background of whole blocks, other than perhaps footer. Thanks.
For the images used, I'd like to stay away from a design studio/digital agency feel and lean more towards professional support and maintenance services. I'm thinking images of content merchants doing their job. Something along the lines of "We'll be taking care of the website so that you only need to care about the business".
Some ideas I like:
http://www.plumframe-pics.example/detail/photo/portrait-of-confident-male-design-professional-royalty-free-image/572048163
http://www.plumframe-pics.example/detail/photo/designer-taking-picture-of-hat-high-res-stock-photography/839207514
http://www.plumframe-pics.example/detail/photo/woman-packaging-pottery-royalty-free-image/216684093
Images of colorful shopping bags and shopping carts are over the top and not serious enough. Instead of images matching Online Shopping, I'd try going more for Stability, Reliability, Performance.
Our existing website is http://www.bravuln.example. Please, don't take design ideas from it, but it will give you a picture of the structure of our new website and content that's going to be used initially.
If you could include a basic icon set to use throughout the website, that would be great. If the icons could match our logo (attached), it would be a big plus.
ALL PAGES
Every page must contain clearly visible phone number (1300 648 907) and a Contact Us Now button, which opens an AJAX driven popup form with Name, Email, Phone and Message to be sent through.
To start with, main menu items will be Torvista, Portfolio, Contact.
At the bottom of each page, please, include a newsletter subscription form with text Subscribe to Torvista Support and Security Updates.
For the footer, I'd like to see a logo strip with the following logos in grayscale (no need to link anywhere): Torvista, QRX, DataVane, NCB. You'll find the logos on Google Images.
Standard footer columns follow. Here, I'd like to see logos in color: Torvista Certified Developer, Torvista Ceritified Solution Provider. Again, the logos are on Google Images.
No social media logos/links necessary anywhere on the website.
...and then the copyright line.
FRONT PAGE
Large slider with images that would appeal to our target audience. Keywords here would be Torvista System Audit, Torvista Performance Optimisation, Torvista Website Emergency Recovery, Torvista Development Infrastructure Hosting. We'll have a static page created for each of these to link to.
In a corner of the slider, or on the edge, can I have an overlay with logos in color (same as footer): Torvista Certified Developer, Torvista Ceritified Solution Provider.
Underneath, a number of blocks, each with an image and teaser that we'll use to link to various pages throughout the website.
PORTFOLIO PAGE
I'm thinking a single long page with a block per client, which will contain project name, description from us and a testimonial from client. Also, each block will contain a single large screenshot. No gallery or slideshow is necessary here, just one image per project.
I'll leave the layout up to you, but try to put yourself in the shoes of a potential client reviewing our past work by simply scrolling down this one page.
CONTACT US PAGE
Separate page with the same form as above, phone number (1300 648 907), email address (support@kavreo.example), address (Suite 42, Level 3|8 Wattlebrook Lane|Fernvale Heights VIC 3999), and a grayscale Google Map.
CODING UP
Coding up into static HTML/CSS/JS is equally important as the design itself. We're a website development company, we'll be integrating the theme. We will spot any issues and we will point them out.
Coded up design must be fully responsive. Enough said.
To be able to create any content in future, we'd like one extra page coded up with samples of all themed elements, lists, forms, buttons, 2, 3, 4-column layout, alerts, icons, etc. This page does not need to be designed, only coded up.
The design will be integrated into Drupal using Twig. If possible at all, try to keep it in mind when designing and coding up, and make the integration into a Drupal theme easier for us.
GOOD LUCK!
That's it. Let me know if anything needs clarifying. So far I've had a great experience with ArtFlockly. I don't doubt some great designs will emerge. Clever ideas are highly appreciated, but also make it clear you've read and followed the points in this brief. Cheers, Tom

```html
<!DOCTYPE html>
<html lang="en">
<head>
<meta charset="utf-8">
<title>Kavreo Commerce – Torvista Development &amp; Support</title>
<link href="https://fonts.googleapis.com/css2?family=Lato:wght@300;400;700&family=Open+Sans:wght@400;600;700&display=swap" rel="stylesheet">
<style>
:root{
  --navy:#0b3a6e;
  --orange:#e67e22;
  --ink:#111;
  --text:#555;
  --muted:#999;
  --band:#3f6a99;
  --panel-dark:#666;
  --footer:#9a9a9a;
  --button-grey:#5b5b5b;
  --white:#fff;
}
*{box-sizing:border-box;margin:0;padding:0}
html,body{width:1200px;height:2384px;overflow:hidden;background:var(--white)}
body{font-family:"Lato",Arial,sans-serif;color:var(--text);position:relative}
section,header,footer{position:absolute;left:0;width:1200px}

/* Header */
.site-header{top:0;height:110px;background:var(--white)}
.brand{position:absolute;left:80px;top:30px;display:flex;align-items:center;gap:12px}
.brand-mark{width:36px;height:36px;background:var(--navy)}
.brand-name{font-family:"Lato",sans-serif;font-weight:700;font-size:34px;color:var(--orange);line-height:1}
.main-nav{position:absolute;top:45px;left:626px;display:flex;gap:0}
.main-nav a{font-size:16px;color:#555;text-decoration:none;letter-spacing:.3px;position:absolute;white-space:nowrap}
.main-nav a.active{color:var(--navy)}

/* Hero */
.hero{top:110px;height:730px;overflow:hidden}
.hero-photo{position:absolute;inset:0;background:linear-gradient(90deg,#ece8e4 0%,#e3ddd6 35%,#cfc6bb 60%,#6d7a92 80%,#e9e5e1 100%)}
.hero-copy{position:absolute;left:80px;top:300px}
.hero-title{font-family:"Lato",sans-serif;font-weight:700;font-size:43px;line-height:65px;color:var(--ink);text-transform:uppercase}
.btn-learn{display:inline-block;margin-top:18px;width:191px;height:56px;line-height:56px;text-align:center;background:var(--orange);color:var(--white);font-size:21px;text-decoration:none}

/* Welcome */
.welcome{top:840px;height:300px;text-align:center}
.welcome-title{margin-top:48px;font-weight:400;font-size:46px;color:var(--navy);letter-spacing:.5px}
.welcome-title span{color:var(--orange)}
.welcome-sub{display:flex;align-items:center;justify-content:center;gap:22px;margin-top:2px;font-size:19px;color:var(--navy)}
.welcome-sub::before,.welcome-sub::after{content:"";width:210px;height:1px;background:var(--navy)}
.welcome-text{width:860px;margin:14px auto 0;font-family:"Open Sans",sans-serif;font-size:15px;line-height:25px;color:var(--text)}

/* Services band */
.services{top:1140px;height:407px;background:linear-gradient(180deg,#3f6a99,#4a76a3);color:var(--white);text-align:center}
.services-title{margin-top:50px;font-weight:400;font-size:36px;letter-spacing:.5px}
.service{position:absolute;top:128px;width:360px;text-align:center}
.service-icon{width:126px;height:126px;margin:0 auto;border:2px solid var(--white);border-radius:50%;display:flex;align-items:center;justify-content:center}
.service-name{margin-top:22px;font-size:20px}
.service-text{margin-top:6px;font-family:"Open Sans",sans-serif;font-size:15px;line-height:25px}

/* Partners */
.partners{top:1547px;height:333px}
.arrow{position:absolute;top:130px;width:42px;height:42px}
.partner-name{position:absolute;left:200px;top:120px;font-family:"Lato",sans-serif;font-weight:300;font-size:52px;color:#222}
.partners-copy{position:absolute;left:636px;top:48px;width:380px}
.partners-title{font-weight:400;font-size:36px;color:#555}
.partners-text{margin-top:10px;font-family:"Open Sans",sans-serif;font-size:20px;line-height:29px;color:var(--muted)}
.btn-read{display:block;margin-top:28px;width:172px;height:50px;line-height:50px;text-align:center;background:var(--button-grey);color:var(--white);font-size:20px;text-decoration:none}

/* Newsletter */
.newsletter{top:1880px;height:149px;background:var(--panel-dark)}
.newsletter-icon{position:absolute;left:80px;top:52px}
.newsletter-label{position:absolute;left:150px;top:62px;font-size:20px;color:var(--white)}
.newsletter-input{position:absolute;left:497px;top:52px;width:417px;height:46px;background:var(--white);border:0;padding-left:16px;font-family:"Open Sans",sans-serif;font-size:17px;color:#999;line-height:46px}
.btn-subscribe{position:absolute;left:914px;top:52px;width:187px;height:46px;line-height:46px;text-align:center;background:var(--navy);color:var(--white);font-size:20px}

/* Footer */
.site-footer{top:2029px;height:355px;background:var(--footer);color:var(--white)}
.footer-heading{position:absolute;top:53px;font-size:17px;font-weight:400;letter-spacing:.3px}
.contact-list{position:absolute;left:80px;top:100px;list-style:none;font-family:"Open Sans",sans-serif;font-size:15px;line-height:24px}
.contact-list li{display:flex;gap:20px;margin-bottom:22px}
.contact-list svg{flex:none;margin-top:4px}
.footer-brand{position:absolute;left:445px;top:120px;display:flex;align-items:center;gap:16px}
.footer-brand .brand-mark{width:50px;height:50px;background:var(--white)}
.footer-brand .brand-name{color:var(--white);font-size:54px}
.partner-grid{position:absolute;left:864px;top:100px;display:grid;grid-template-columns:130px 130px;row-gap:36px;font-family:"Lato",sans-serif;font-weight:700;font-size:22px}
.copyright{position:absolute;left:0;right:0;bottom:32px;text-align:center;font-family:"Open Sans",sans-serif;font-size:14px}
.copyright strong{font-weight:700}
</style>
</head>
<body>

<header class="site-header">
  <div class="brand"><span class="brand-mark"></span><span class="brand-name">Kavreo</span></div>
  <nav class="main-nav">
    <a class="active" href="#" style="left:0">HOME</a>
    <a href="#" style="left:102px">ABOUT US</a>
    <a href="#" style="left:239px">PORTFOLIO</a>
    <a href="#" style="left:380px">CONTACT US</a>
  </nav>
</header>

<section class="hero">
  <div class="hero-photo" role="img" aria-label="Smiling professional in glasses and checked shirt talking on the phone in a bright office"></div>
  <div class="hero-copy">
    <h1 class="hero-title">Get started with world's<br>leading ecommerce platform</h1>
    <a class="btn-learn" href="#">LEARN MORE</a>
  </div>
</section>

<section class="welcome">
  <h2 class="welcome-title">WELCOME TO KAVREO <span>COMMERCE</span></h2>
  <p class="welcome-sub">Leading eCommerce Platform</p>
  <p class="welcome-text">We're a Melbourne based website development company. We specialise exclusively in Torvista e-commerce platform. What distinguishes our business from competition is that rather than designing and building brand new websites, we offer development, support and maintenance services to established websites. Maintenance and Support are the keywords representing our business.</p>
</section>

<section class="services">
  <h2 class="services-title">ECOMMERCE BY KAVREO</h2>
  <div class="service" style="left:35px">
    <div class="service-icon">
      <svg width="56" height="50" viewBox="0 0 56 50" fill="none" stroke="#fff" stroke-width="4" stroke-linejoin="round"><path d="M2 4h9l6 28h30l5-20H14"/><circle cx="22" cy="43" r="4" fill="#fff"/><circle cx="42" cy="43" r="4" fill="#fff"/></svg>
    </div>
    <h3 class="service-name">Why Kavreo?</h3>
    <p class="service-text">Fast Torvista-based online stores, built<br>on time and to specification.</p>
  </div>
  <div class="service" style="left:421px">
    <div class="service-icon">
      <svg width="44" height="44" viewBox="0 0 44 44"><rect x="8" y="8" width="28" height="28" fill="#fff"/></svg>
    </div>
    <h3 class="service-name">Why Torvista?</h3>
    <p class="service-text">Torvista is the world's leading open<br>source eCommerce platform.</p>
  </div>
  <div class="service" style="left:787px">
    <div class="service-icon">
      <svg width="52" height="52" viewBox="0 0 52 52"><g fill="#fff"><circle cx="26" cy="26" r="16"/><rect x="22" y="4" width="8" height="44"/><rect x="4" y="22" width="44" height="8"/><rect x="22" y="4" width="8" height="44" transform="rotate(45 26 26)"/><rect x="22" y="4" width="8" height="44" transform="rotate(-45 26 26)"/></g><circle cx="26" cy="26" r="7" fill="#4a76a3"/></svg>
    </div>
    <h3 class="service-name">What we do ?</h3>
    <p class="service-text">From support, maintenance and<br>upgrades to redesigns.</p>
  </div>
</section>

<section class="partners">
  <svg class="arrow" style="left:77px" viewBox="0 0 42 42" fill="none" stroke="#333" stroke-width="1.5"><circle cx="21" cy="21" r="20"/><path d="M24 13l-8 8 8 8"/></svg>
  <p class="partner-name">Lacewell</p>
  <div class="partners-copy">
    <h2 class="partners-title">OUR PARTNERS</h2>
    <p class="partners-text">Kavreo are great devlopers whise concentration on detail does not compromise the delivery of work</p>
    <a class="btn-read" href="#">Read More</a>
  </div>
  <svg class="arrow" style="left:1081px" viewBox="0 0 42 42" fill="none" stroke="#333" stroke-width="1.5"><circle cx="21" cy="21" r="20"/><path d="M18 13l8 8-8 8"/></svg>
</section>

<section class="newsletter">
  <svg class="newsletter-icon" width="50" height="38" viewBox="0 0 50 38" fill="none" stroke="#fff" stroke-width="3"><rect x="2" y="2" width="46" height="34" rx="5"/><path d="M4 5l21 17L46 5"/></svg>
  <p class="newsletter-label">Join the newsletter &amp; stay informed</p>
  <div class="newsletter-input">Enter Email</div>
  <div class="btn-subscribe">SUBSCRIBE</div>
</section>

<footer class="site-footer">
  <h4 class="footer-heading" style="left:83px">CONTACT</h4>
  <ul class="contact-list">
    <li><svg width="14" height="18" viewBox="0 0 14 18"><path d="M7 0a7 7 0 0 1 7 7c0 5-7 11-7 11S0 12 0 7a7 7 0 0 1 7-7z" fill="#fff"/><circle cx="7" cy="7" r="2.5" fill="#9a9a9a"/></svg><span>Suite 42, Level 3|8 Wattlebrook Lane<br>|Fernvale Heights VIC 3999</span></li>
    <li><svg width="16" height="12" viewBox="0 0 16 12" fill="none" stroke="#fff" stroke-width="1.5"><rect x="1" y="1" width="14" height="10" rx="1.5"/><path d="M1.5 2l6.5 5 6.5-5"/></svg><span>support@kavreo.example</span></li>
    <li><svg width="15" height="15" viewBox="0 0 15 15"><path d="M3 0l3 3.5-2 2c1 2 3 4 5 5l2-2 3.5 3-2 2.5C7 14 1 8 .5 2.5z" fill="#fff"/></svg><span>1300 648 907</span></li>
  </ul>
  <div class="footer-brand"><span class="brand-mark"></span><span class="brand-name">Kavreo</span></div>
  <h4 class="footer-heading" style="left:864px">OUR PARTNERS</h4>
  <div class="partner-grid">
    <span>Torvista</span><span>QRX</span>
    <span>NCB</span><span>DataVane</span>
  </div>
  <p class="copyright"><strong>@ KAVREO COMMERCE</strong> 2016 | All Rights Reserved</p>
</footer>

</body>
</html>
```